Label for Sugar Scrub, sugar peeling

We need a label for a SugarScrub can. We produce both sugar and salt scrubs for B2C and B2B. The market is more dominated by women, but we also want to bring the men on board. In addition to the logo as a font may also fit a picture, a silhouette o.ä. be introduced. Overall, it should be structured rather clearly, more masculine than too flowery and simply modern. It may be multicolored, but not too colorful. The high quality should be highlighted by the design, as it is more in the upper price segment settled. Since we work only with natural "100% Organic" ingredients, it may also be colored accordingly. There will be different fragrances. As an example files, I would attach rosemary lemon. But it should also be a variety of compositions austere nature, other fruits such as grapefruit, lime, etc. are produced. The dimensions of the product label are 25 x 250 mm (WxH). A round logo for the lid is to be designed with 78mm diameter matching, but only logo, the image of the scent direction and the fragrance name or the words "Sugar Scrub" included. As a box will serve, inter alia, a bamboo can, but also a semi-transparent plastic can be used. The sale takes place both online, as in beauty salons and hotels as a product in the exhibition. The label is white or transparent for the plastic box, but only transparent for the bamboo box. In the course I can gladly send the company logo by e-mail. At first I do not want to give away too much. The sample texts for the label are included in the appendix. All in all, however, I would like to give free rein to the freedom of design and not limit too much. Questions can be asked at any time, I will try to answer as soon as possible. However, the project should be open until 16.04. reasonably stand. Otherwise, I can probably only from 18.04. reply.

Target Market(s)

Target market are end users, B2B customers (sauna operators, hotels) and customers of beauty salons.

Font styles to use
Sans Serif

Requirements
Must have
• The three blocks "Ingredients, Logo, Application Recommendation" must be clearly arranged. My logo has the colors (RGB): 63, 148,167 4, 4, 4 152, 152, 152
Nice to have
• It would be nice if it has a rather clear design that appeals to men as well. Possibly. Maybe just by a different color choice could be minted on women.
Should not have
• Not specified....

```html
<!DOCTYPE html>
<html lang="de">
<head>
<meta charset="utf-8">
<title>Kalmora Zuckerpeeling – Etikett</title>
<link href="https://fonts.googleapis.com/css2?family=Fira+Sans+Extra+Condensed:wght@400;500;600&family=Montserrat:wght@500;600&display=swap" rel="stylesheet">
<style>
  :root {
    --stage: #282828;
    --label: #ffffff;
    --teal: #3f94a7;
    --ink: #040404;
    --grey: #989898;
    --green: #8dc63f;
    --green-soft: #eef6e2;
    --lemon-light: #fbf3a0;
    --lemon-deep: #ecd94f;
  }
  * { margin: 0; padding: 0; box-sizing: border-box; }
  html, body { width: 1200px; height: 794px; overflow: hidden; background: var(--stage); }
  .label {
    position: absolute; left: 45px; top: 342px;
    width: 1110px; height: 110px;
    background: var(--label);
    font-family: "Fira Sans Extra Condensed", "Arial Narrow", sans-serif;
  }
  .ingredients {
    position: absolute; left: 56px; top: 13px; width: 262px;
    font-size: 9.5px; line-height: 1.4; color: var(--grey); font-weight: 500;
  }
  .facts {
    position: absolute; left: 56px; top: 62px;
    font-size: 9.5px; line-height: 1.4; color: var(--ink); font-weight: 600;
  }
  .band {
    position: absolute; left: 409px; top: 72px; width: 262px; height: 22px;
    background: var(--ink); color: #fff;
    font-family: "Montserrat", sans-serif; font-weight: 600;
    font-size: 8.5px; letter-spacing: 2px;
    display: flex; align-items: center; justify-content: center;
    padding-left: 30px; padding-right: 10px;
  }
  .seal {
    position: absolute; left: 354px; top: 19px;
    width: 78px; height: 78px; border-radius: 50%;
    background: var(--green-soft);
    border: 4px solid var(--green);
  }
  .brand {
    position: absolute; left: 470px; top: 12px; width: 170px; text-align: center;
    font-family: "Montserrat", sans-serif; font-weight: 500;
    font-size: 21px; line-height: 26px; color: var(--teal);
  }
  .brand-dot {
    display: inline-block; width: 6px; height: 6px; border-radius: 50%;
    background: var(--grey); vertical-align: top; margin-left: 3px; margin-top: 2px;
  }
  .product {
    position: absolute; left: 458px; top: 45px; width: 190px; text-align: center;
    font-family: "Montserrat", sans-serif; font-weight: 500;
    font-size: 17.5px; line-height: 22px; letter-spacing: 0.3px; color: var(--ink);
  }
  .scent-art {
    position: absolute; left: 640px; top: 14px; width: 88px; height: 86px;
    border-radius: 8px;
    background: linear-gradient(135deg, var(--lemon-light), var(--lemon-deep));
  }
  .usage {
    position: absolute; left: 781px; top: 25px; width: 284px;
    font-size: 9.5px; line-height: 1.4; color: var(--grey); font-weight: 500;
  }
</style>
</head>
<body>
  <section class="label">
    <div class="ingredients">
      Zutaten: Lorem ipsum dolor sit amet, consetetur sadipscing elitr, sed diam nonumy eirmod<br>
      tempor invidunt ut labore et dolore magna aliquyam erat
    </div>
    <div class="facts">
      360 gr Netto<br>
      MHD: 12/2019<br>
      Recycling Zeichen, Kunststoffbezeichnung
    </div>

    <div class="band">ROSMARIN-ZITRONE</div>
    <div class="seal" role="img" aria-label="Platz für das Bio-Siegel"></div>
    <div class="brand">Kalmora<span class="brand-dot"></span></div>
    <div class="product">ZUCKERPEELING</div>
    <div class="scent-art" role="img" aria-label="Bild einer Zitronenscheibe als Duftmotiv"></div>

    <div class="usage">
      Anwendungshinweis: Nach dem Duschen oder der Sauna anwenden. Haut von überschüssigem Wasser befreien und Peeling kreisend auf die noch feuchte Haut kreisend einmassieren, bis es sich aufgelöst hat. Warm abduschen und Haut mit Handtuch trocken tupfen.
    </div>
  </section>
</body>
</html>
```